Personalized Technology Company Needs a Business Card

I need a double-sided business card. Both sides will have the logo, and the contact information. One side will be black, with the white / gray logo, and the other will be white, with the black / gray logo. The black side will have the text "Custom Gaming PC's" and will have a water-cooled gaming PC image. The white side will have the text "Custom Business Computers & Consulting", and will have a business / enterprise PC image. Feel free to add a conservative image in the background, while the color remains unchanged. I'm uploading the base logo (transparent), so you can modify the colors, both the finished colored logos and an idea of ​​the business card (with the current information, just missing the website, which is www.velomindsystems.com, please add it.) Thank you so much for your effort, I'll be specting your cool designs. Good Luck!

Target Market(s)

Gamers & Entrepreneurs / Business Owners / Chief Technology Officers

Industry/Entity Type

Technology Equipment

Contact Information for Business Card

I need a double-sided business card. Both sides will have the logo, and the contact information. One side will be black, with the white/gray logo, and the other one will be white, with the black/gray logo. The black side will have the text "Custom Gaming PC's" and will have a water-cooled gaming PC image. The white side will have the text "Custom Business Computers & Consulting", and will have a business/enterprise PC image. Feel free to add a conservative image in the background, whilst the color remains unchanged.

I'm uploading the base logo (transparent), so you can modify the colors, both the finished colored logos and an idea of the business card (with the actual information, just missing the website, which is www.velomindsystems.com, please add it.)

Thank you so much for your effort, I'll be specting your cool designs. Good Luck!

Font styles to use
Serif

Colors
000000
757575
ffffff

Requirements
Must have
• Please See Description
Nice to have
• Please See Description
Should not have
• Please See Description

```html
<!DOCTYPE html>
<html lang="en">
<head>
<meta charset="utf-8">
<title>Velomind Systems – Business Card</title>
<link href="https://fonts.googleapis.com/css2?family=Lato:wght@400;700&display=swap" rel="stylesheet">
<style>
  :root {
    --ink: #000000;
    --stone: #757575;
    --paper: #ffffff;
    --card-white: #f7f6f5;
    --edge-beige: #d6cfc4;
    --backdrop: #e9e7e4;
  }
  * { box-sizing: border-box; margin: 0; padding: 0; }
  html, body {
    width: 1200px; height: 900px; overflow: hidden;
    background: var(--backdrop);
    font-family: "Lato", sans-serif;
  }
  .card {
    position: absolute; left: 120px; top: 152px;
    width: 960px; height: 596px;
    background: var(--card-white);
    box-shadow: 0 10px 30px rgba(0,0,0,.18);
    overflow: hidden;
  }
  .card__panel { position: absolute; inset: 0; }
  .holder { position: absolute; left: 54px; top: 74px; color: var(--ink); }
  .holder__name { font-size: 32px; font-weight: 700; letter-spacing: .5px; line-height: 1.1; }
  .holder__role { font-size: 23px; font-weight: 400; margin-top: 6px; }
  .contacts {
    position: absolute; left: 54px; top: 418px;
    list-style: none; color: var(--ink); font-size: 21px; line-height: 33px;
  }
  .contacts li { display: flex; align-items: center; gap: 8px; }
  .contacts svg { width: 16px; height: 16px; flex: none; }
  .services {
    position: absolute; right: 53px; top: 122px; text-align: right;
    color: var(--paper); font-size: 25px; font-weight: 700; line-height: 43px; letter-spacing: .8px;
  }
  .brand {
    position: absolute; left: 520px; top: 372px; width: 390px;
    display: flex; align-items: center; gap: 14px;
    color: var(--paper); font-size: 34px; font-weight: 700; letter-spacing: 3px;
  }
  .brand__dot { width: 26px; height: 26px; border-radius: 50%; background: var(--paper); flex: none; }
  .tagline {
    position: absolute; left: 560px; top: 498px; width: 380px; text-align: center;
    color: var(--paper); font-size: 23px; font-weight: 400; letter-spacing: .5px;
  }
</style>
</head>
<body>
  <div class="card">
    <svg class="card__panel" viewBox="0 0 960 596" width="960" height="596" aria-hidden="true">
      <path transform="translate(-12,6)" fill="var(--edge-beige)"
        d="M723 0 H972 V596 H576 C470 560 400 470 400 360 C400 230 470 90 600 40 C650 20 690 8 723 0 Z"/>
      <path fill="var(--ink)"
        d="M723 0 H960 V596 H576 C470 560 400 470 400 360 C400 230 470 90 600 40 C650 20 690 8 723 0 Z"/>
    </svg>

    <div class="holder">
      <p class="holder__name">DANIEL REYES MORO</p>
      <p class="holder__role">CEO &amp; Co-Founder</p>
    </div>

    <ul class="contacts">
      <li><svg viewBox="0 0 16 16"><path fill="currentColor" d="M2 5c0-2 2-3 6-3s6 1 6 3v1h-3V5H5v1H2zM4 7h8l2 6H2z"/></svg>52 5184-2093</li>
      <li><svg viewBox="0 0 16 16"><rect x="4" y="1" width="8" height="14" rx="1.5" fill="none" stroke="currentColor" stroke-width="1.6"/><circle cx="8" cy="12.5" r="1" fill="currentColor"/></svg>+52 55-6401-8357</li>
      <li><svg viewBox="0 0 16 16"><rect x="1" y="3" width="14" height="10" fill="currentColor"/><path d="M1 3l7 6 7-6" fill="none" stroke="var(--card-white)" stroke-width="1.2"/></svg>contact@velomindsystems.com</li>
      <li><svg viewBox="0 0 16 16"><circle cx="8" cy="8" r="7" fill="currentColor"/><path d="M1 8h14M8 1c3 3 3 11 0 14M8 1c-3 3-3 11 0 14" fill="none" stroke="var(--card-white)" stroke-width=".9"/></svg>www.velomindsystems.com</li>
    </ul>

    <p class="services">CUSTOM BUSINESS<br>COMPUTERS &amp;<br>CONSULTING</p>

    <div class="brand"><span class="brand__dot"></span><span>VELOMIND SYSTEMS</span></div>

    <p class="tagline">CUSTOM GAMING PC'S</p>
  </div>
</body>
</html>
```